Business card for denture clinic Veltrimora

We need a new business card with our new logo. We are a denture clinic in New Zealand with our target market being 45+ years old. We would need a space on the back to write our patients next appointment on. We would space for only one appointment rather than a list. We will attach a photo showing an example of this. But of course, we would like to see your twist on this. We want it to be bold and easy to read and a good mixture of professional but modern. We have attached our logo to be used on the card.

Target Market(s)

People aged 45+ needing dentures

Industry/Entity Type

Dental

Contact Information for Business Card

We want our logo on the front and the space to write an appointment on the back. I've attached an example our our old business card showing this. We need to have the technicians details on the front.

Font styles to use
Sans Serif

Colors
0255a3
919191
fbfbfb

Requirements
Must have
• The following details:
• Liam Dorsett BDT, PGDipCDentTech Calverin
• Dental Prosthetist
• Phone numbers: 0800 47 3125
• 09 572 1394
• Email: liam@veltrimora.co.nz
• www.veltrimora.co.nz
• Address: 14 Marlow Crest Road
• Halbrook West
• Auckland 0793
Nice to have
• We would like our business cards to have more than just two colours as we want them to be more vibrant. We have uploaded an example of a business card we liked that showed this.

```html
<!DOCTYPE html>
<html lang="en">
<head>
<meta charset="utf-8">
<title>Veltrimora Business Card</title>
<link rel="stylesheet" href="https://fonts.googleapis.com/css2?family=Lato:ital,wght@0,400;0,700;0,900;1,400&display=swap">
<style>
  :root {
    --brand-blue: #0262a3;
    --ink: #1b1b1b;
    --grey: #919191;
    --card: #fbfbfb;
    --stage: #ececec;
    --white: #ffffff;
  }
  * { margin: 0; padding: 0; box-sizing: border-box; }
  html, body {
    width: 1200px; height: 586px; overflow: hidden;
    background: var(--stage);
    font-family: "Lato", Arial, sans-serif;
  }
  .canvas { position: relative; width: 1200px; height: 586px; }
  .card {
    position: absolute; top: 129px;
    width: 502px; height: 301px;
    background: var(--card);
    overflow: hidden;
  }
  .card--back { left: 61px; }
  .card--front { left: 619px; }

  /* Back: appointment side */
  .appointment-title {
    position: absolute; left: 0; width: 100%; top: 38px;
    text-align: center;
  }
  .appointment-title span {
    display: inline-block;
    color: var(--brand-blue);
    font-weight: 700; font-size: 13px;
    letter-spacing: 4.2px;
    padding: 0 1px 2px;
    border-bottom: 1px solid var(--brand-blue);
  }
  .field-label {
    position: absolute; top: 109px;
    color: var(--brand-blue); font-size: 12.5px;
  }
  .field-box {
    position: absolute; top: 133px;
    width: 190px; height: 40px;
    border: 3px solid var(--brand-blue);
    border-radius: 9px;
    background: var(--white);
  }
  .label-date { left: 39px; }
  .box-date { left: 41px; }
  .label-time { left: 273px; }
  .box-time { left: 274px; }
  .stripe {
    position: absolute; left: 0; width: 100%; height: 3px;
    background: var(--brand-blue);
  }
  .stripe-one { top: 208px; }
  .stripe-two { top: 215px; }
  .brand-band {
    position: absolute; left: 0; top: 222px;
    width: 100%; height: 79px;
    background: var(--brand-blue);
    color: var(--white); text-align: center;
  }
  .brand-band .brand-name {
    margin-top: 17px;
    font-size: 25px; font-weight: 700;
    letter-spacing: 1.5px; line-height: 28px;
    text-transform: uppercase;
  }
  .brand-band .brand-tagline {
    font-size: 11px; font-weight: 700;
    letter-spacing: 2.6px; line-height: 16px;
  }

  /* Front: details side */
  .logo-mark {
    position: absolute; left: 231px; top: 26px;
    width: 39px; height: 39px;
    background: var(--brand-blue);
  }
  .logo-name {
    position: absolute; left: 0; width: 100%; top: 66px;
    text-align: center;
    color: var(--brand-blue);
    font-size: 22px; font-weight: 700; letter-spacing: 1.2px;
    line-height: 24px; text-transform: uppercase;
  }
  .logo-tagline {
    position: absolute; left: 0; width: 100%; top: 88px;
    text-align: center;
    color: var(--grey);
    font-size: 9px; letter-spacing: 2.2px; line-height: 11px;
  }
  .person-name {
    position: absolute; left: 25px; top: 128px;
    color: var(--brand-blue); font-size: 15.5px; font-weight: 900;
    line-height: 20px;
  }
  .person-credential {
    position: absolute; left: 25px; top: 151px;
    color: var(--ink); font-size: 10.5px; font-style: italic;
  }
  .pill {
    position: absolute; top: 170px; height: 15px;
    background: var(--brand-blue); color: var(--white);
    font-size: 10.5px; font-weight: 700; line-height: 15px;
  }
  .pill-role {
    left: 0; width: 139px; padding-left: 26px;
    border-radius: 0 8px 8px 0;
  }
  .pill-hours {
    right: 0; width: 125px; padding-left: 12px;
    border-radius: 8px 0 0 8px;
  }
  .hours {
    position: absolute; right: 36px; top: 191px;
    text-align: right; color: var(--ink);
    font-size: 11.5px; line-height: 21px;
  }
  .hours strong { font-weight: 700; }
  .address {
    position: absolute; right: 36px; top: 246px;
    text-align: right; color: var(--brand-blue);
    font-size: 12.5px; font-weight: 700; line-height: 18px;
  }
  .contact-list { position: absolute; left: 24px; top: 212px; list-style: none; }
  .contact-item {
    display: flex; align-items: center;
    height: 18px; margin-bottom: 6px;
    font-size: 12px; color: var(--ink);
  }
  .contact-icon { width: 17px; height: 17px; margin-right: 8px; flex: none; }
</style>
</head>
<body>
<main class="canvas">

  <section class="card card--back" aria-label="Appointment side">
    <h2 class="appointment-title"><span>Your Next Appointment</span></h2>
    <p class="field-label label-date">Date:</p>
    <div class="field-box box-date"></div>
    <p class="field-label label-time">Time:</p>
    <div class="field-box box-time"></div>
    <div class="stripe stripe-one"></div>
    <div class="stripe stripe-two"></div>
    <div class="brand-band">
      <p class="brand-name">Veltrimora</p>
      <p class="brand-tagline">THE DENTURE EXPERTS</p>
    </div>
  </section>

  <section class="card card--front" aria-label="Contact side">
    <div class="logo-mark"></div>
    <p class="logo-name">Veltrimora</p>
    <p class="logo-tagline">THE DENTURE EXPERTS</p>

    <h1 class="person-name">Liam Dorsett BDT</h1>
    <p class="person-credential">PGDipCDentTech Calverin</p>
    <p class="pill pill-role">Dental Prosthetist</p>
    <p class="pill pill-hours">Opening Hours</p>

    <ul class="contact-list">
      <li class="contact-item">
        <svg class="contact-icon" viewBox="0 0 20 20" aria-hidden="true">
          <circle cx="10" cy="10" r="10" fill="#0262a3"/>
          <path d="M5 8.5c0-1.5 2.2-2.5 5-2.5s5 1 5 2.5v1h-2.5v-1.2h-5v1.2H5z M6.5 11h7l1 3.5h-9z" fill="#fff"/>
        </svg>
        0800 47 3125
      </li>
      <li class="contact-item">
        <svg class="contact-icon" viewBox="0 0 20 20" aria-hidden="true">
          <circle cx="10" cy="10" r="10" fill="#0262a3"/>
          <path d="M5 8.5c0-1.5 2.2-2.5 5-2.5s5 1 5 2.5v1h-2.5v-1.2h-5v1.2H5z M6.5 11h7l1 3.5h-9z" fill="#fff"/>
        </svg>
        09 572 1394
      </li>
      <li class="contact-item">
        <svg class="contact-icon" viewBox="0 0 20 20" aria-hidden="true">
          <circle cx="10" cy="10" r="10" fill="#0262a3"/>
          <rect x="5" y="6.5" width="10" height="7" fill="#fff"/>
          <path d="M5 6.5l5 4 5-4" fill="none" stroke="#0262a3" stroke-width="1"/>
        </svg>
        liam@veltrimora.co.nz
      </li>
    </ul>

    <p class="hours">
      <strong>Mon - Thurs:</strong> 9.00am - 5.00pm<br>
      <strong>Fri - Sat:</strong> 9.00am - 1.00pm
    </p>
    <p class="address">14 Marlow Crest Road<br>Halbrook West Auckland 0793</p>
  </section>

</main>
</body>
</html>
```